Counselling business needs a DL brochure design ready for print next week!

My business is called Quiet Harbour Counselling. My name is Megan Trelawny and I'm a qualified Psychotherapist based in Sydney, Australia.

I need a DL brochure to promote my business. I like the idea of possibly incorporating a leaf/leaves and/or the colour green in a sophisticated, understated way in the DL design. I have attached a leaf image for reference. I am looking for a simple, elegant design overall. Not too many fonts, something which is easy to read and captures people's interest.

I need a print ready design - something that my local instant printer can use easily. I need a print ready PDF and original files too for the printer. I am anticipating that the design will be A4 folded to DL as it needs to fit into standard dimension plastic DL stands at various locations.

My business is focussed upon helping people overcome difficulties such as grief or anxiety. I also work with people to help them plan their life adventures. My business is different from the average counselling business. For example, I give my clients a beautiful thick stock postcard at the end of every session with takeaway learnings and insights which they've uncovered. That way, they can reflect upon those discoveries and capitalise upon them.

I have an office in a local wellness centre. The brochure will be showcased at the centre and in local medical centres and shops. The aim is that new prospects will pick up the brochure and be prompted to call me for a counselling appointment.

I have attached copy for my DL brochure and a competitor's DL for reference. I'm not seeking to emulate the competitor, but I thought that it could be a useful reference - the competitor DL is clear and easy to read. I need my photo to be included in the brochure, adjacent to the information about my background. I have attached a reference photo for use as a positional - a full size image will need to be dropped in as part of this job by the winning designer.

I do not have a company logo at the moment, but I need my business name and contact details repeated several times in the DL.
Updates

Hello. Thank you for your designs. I am so pleased to have received them. I will be in touch in the next 24 hours. Best, Megan

Industry/Entity Type

Business

```html
<!DOCTYPE html>
<html lang="en">
<head>
<meta charset="utf-8">
<title>Quiet Harbour Counselling – DL Brochure</title>
<link rel="stylesheet" href="https://fonts.googleapis.com/css2?family=Mulish:ital,wght@0,700;1,500;1,600;1,700&display=swap">
<style>
  :root {
    --green: #8ab43f;
    --green-pale: #c9dca6;
    --ink: #454545;
    --paper: #ffffff;
    --mist: #eff0f2;
    --backdrop: #e9e6e1;
  }
  html, body { margin: 0; padding: 0; }
  body {
    width: 1200px; height: 861px; overflow: hidden;
    background: var(--backdrop);
    font-family: "Mulish", Arial, sans-serif;
  }
  .brochure {
    position: absolute; left: 44px; top: 38px;
    width: 1112px; height: 785px;
    background: var(--paper);
    box-shadow: 0 2px 10px rgba(0,0,0,.15);
    overflow: hidden;
  }
  .shapes { position: absolute; inset: 0; }
  .fold { position: absolute; top: 0; bottom: 0; width: 1px; background: rgba(0,0,0,.08); }

  /* Panel 1 – questions */
  .questions {
    position: absolute; left: 0; top: 66px; width: 370px;
    text-align: center; font-style: italic; font-weight: 600;
    font-size: 17.5px; line-height: 23.5px;
  }
  .questions p { margin: 0 0 14px; }
  .questions .accent { color: var(--green); }
  .questions .plain { color: var(--ink); }
  .session-photo {
    position: absolute; left: 39px; top: 549px; width: 293px; height: 159px;
    background: linear-gradient(120deg, #a9b4bd, #dfe3e6 55%, #c7b49a);
  }

  /* Panel 2 – cover inside */
  .mark { position: absolute; border-radius: 50%; }
  .headline {
    position: absolute; left: 370px; top: 144px; width: 372px;
    text-align: center; color: var(--ink);
    font-style: italic; font-weight: 600; font-size: 22px; line-height: 32px; margin: 0;
  }
  .tag-box {
    position: absolute; background: var(--green); color: #fff;
    font-style: italic; font-weight: 600; font-size: 24px;
    display: flex; align-items: center; justify-content: center;
  }
  .brand-name {
    position: absolute; font-weight: 700; font-size: 24px; line-height: 30px;
    letter-spacing: .5px; margin: 0;
  }
  .brand-name.on-green { color: #fff; }
  .brand-name.on-mist { color: var(--ink); }
  .contact {
    position: absolute; left: 398px; top: 658px; list-style: none; margin: 0; padding: 0;
    color: #fff; font-style: italic; font-weight: 700;
  }
  .contact li { display: flex; align-items: center; gap: 9px; }
  .contact .phone { font-size: 22px; height: 34px; margin-bottom: 6px; }
  .contact .mail, .contact .web { font-size: 16px; height: 36px; }
  .contact svg { flex: none; }

  /* Panel 3 – front cover */
  .beach-photo { position: absolute; left: 742px; top: 0; width: 370px; height: 785px; }
  .tagline {
    position: absolute; left: 760px; top: 654px; margin: 0;
    color: #fff; font-style: italic; font-weight: 600; font-size: 22px; line-height: 40px;
  }
</style>
</head>
<body>
<main class="brochure">

  <svg class="shapes" width="1112" height="785" viewBox="0 0 1112 785" aria-hidden="true">
    <defs>
      <linearGradient id="sky" x1="0" y1="0" x2="0" y2="1">
        <stop offset="0" stop-color="#c9d5e2"/>
        <stop offset=".45" stop-color="#eef1f5"/>
        <stop offset=".7" stop-color="#d7dde4"/>
        <stop offset="1" stop-color="#e7e3dc"/>
      </linearGradient>
    </defs>
    <!-- panel 1 chevron bands -->
    <polygon points="0,0 370,0 370,10 185,44 0,10" fill="var(--mist)"/>
    <polygon points="0,785 370,785 370,765 185,737 0,765" fill="var(--green)"/>
    <!-- panel 2 light wedge -->
    <polygon points="560,475 742,300 742,576" fill="var(--mist)"/>
  </svg>

  <div class="beach-photo" role="img" aria-label="Photo of a woman with arms outstretched on a bright beach"
       style="background: linear-gradient(180deg, #c9d5e2, #eef1f5 45%, #d7dde4 70%, #e7e3dc);"></div>

  <svg class="shapes" width="1112" height="785" viewBox="0 0 1112 785" aria-hidden="true">
    <polygon points="742,576 1112,359 1112,785 742,785" fill="var(--mist)"/>
    <polygon points="370,369 1112,785 370,785" fill="var(--green)"/>
  </svg>

  <div class="fold" style="left:370px"></div>
  <div class="fold" style="left:742px"></div>

  <!-- Panel 1 -->
  <section class="questions">
    <p class="accent">DO YOU NEED<br>A POSITIVE CHANGE?</p>
    <p class="plain">DO YOU WISH You felt<br>more joyful and fulfilled?</p>
    <p class="accent">You felt less stressed<br>or overwhelmed?</p>
    <p class="plain">You coped better with<br>life’s challenges?</p>
    <p class="accent">You could break unhelpful habits?</p>
    <p class="plain">DO YOU IMAGINE Your<br>relationships being closer?</p>
    <p class="accent">Your life being well balanced?</p>
    <p class="plain">Your goals being within reach?</p>
    <p class="accent">Your life being more adventurous?</p>
  </section>
  <div class="session-photo" role="img" aria-label="Photo of a client talking with a counsellor who takes notes"></div>

  <!-- Panel 2 -->
  <span class="mark" style="left:517px;top:39px;width:78px;height:78px;background:var(--green)"></span>
  <h2 class="headline">The Power To Create New<br>Possibilities Is Within You.</h2>
  <div class="tag-box" style="left:411px;top:228px;width:292px;height:46px">You Might Just Need</div>
  <div class="tag-box" style="left:420px;top:279px;width:270px;height:45px">A Helping Hand</div>

  <span class="mark" style="left:435px;top:481px;width:78px;height:78px;background:#fff"></span>
  <p class="brand-name on-green" style="left:398px;top:575px">QUIET HARBOUR<br>COUNSELLING</p>

  <ul class="contact">
    <li class="phone">
      <svg width="16" height="18" viewBox="0 0 16 18"><path d="M4 1 L7 5 L5 7 C6 10 8 12 10 13 L12 11 L15 14 L13 17 C7 16 2 10 1 4 Z" fill="#fff"/></svg>
      0400 555 213
    </li>
    <li class="mail">
      <svg width="16" height="12" viewBox="0 0 16 12"><rect x="0" y="0" width="16" height="12" rx="1" fill="#fff"/><path d="M1 1 L8 7 L15 1" stroke="var(--green)" stroke-width="1.5" fill="none"/></svg>
      hello@quietharbourcounselling.com
    </li>
    <li class="web">
      <svg width="15" height="15" viewBox="0 0 16 16" fill="none" stroke="#fff" stroke-width="1.4"><circle cx="8" cy="8" r="7"/><ellipse cx="8" cy="8" rx="3" ry="7"/><path d="M1 8 H15 M2.5 4.5 H13.5 M2.5 11.5 H13.5"/></svg>
      www.quietharbourcounselling.com
    </li>
  </ul>

  <!-- Panel 3 -->
  <span class="mark" style="left:826px;top:537px;width:78px;height:78px;background:var(--green)"></span>
  <p class="brand-name on-mist" style="left:916px;top:552px;font-size:19px;line-height:26px">QUIET HARBOUR<br>COUNSELLING</p>
  <p class="tagline">Overcome<br>Difficulties and<br>Make A Fresh Start</p>

</main>
</body>
</html>
```